Calendar Design Project: 2025 with Specific Edits

This is a straightforward project where your creativity can shine!
Simply take the existing 2024 calendar and adapt it for 2025 by incorporating the new photos I've attached.
Please keep the overall concept of the 2024 calendar intact—your focus will be on enhancing it with fresh visuals.

I can't wait to see your amazing designs!
I am looking for a talented graphic designer to create a new 2025 calendar with specific adjustments.
Pictures attached.
Requirements:
Calendar Size: 52cm x 34cm
March Folder:
Adjust the image named "attached - DJI-0025" to make the circular road darker to match the rest of the design.
May Folder:
Modify the circled area in the May image to ensure it looks consistent with the other road (reference file: "attached - After").
November Folder:
Clear out the circled area in the November image (reference file: "attached - After1").
Please let me know if you have any questions or need further clarification.
I added to my breif a design i made last year for same client.
2025, calendar should be vertical and not horizontal. and some of the photos attache are "Before" and "After" please include together inside each month of the calendar.
Thank you!
Feel free to adjust any details as necessary!

Hello talented designers!

I’m excited to share that this is my 14th project on the ArtHive platform, and I’ve been fortunate to have successful collaborations in the past. I'm looking forward to creating a new 2025 calendar with your help, and I believe that with your creativity and skills, we can make this project a success as well!

I hope to establish a long-term relationship with a talented team like yours. As an added incentive, I will be offering a bonus for the winner, and I may select more than one winner, so everyone has a chance to shine!

Let’s make something amazing together!

Best
Update:
cancel or before, only place the After picture

Requirements
Must have
• Project Overview Objective: Create a 2025 calendar using the provided images, maintaining the design concept from the 2024 calendar but enhancing it with new visuals. Format: Vertical layout (52cm x 34cm).

```html
<!DOCTYPE html>
<html lang="en">
<head>
<meta charset="utf-8">
<title>Torvan Construction 2025 Calendar</title>
<link href="https://fonts.googleapis.com/css2?family=Archivo+Black&family=Saira+Condensed:wght@500;700&family=Montserrat:wght@500&family=Alfa+Slab+One&display=swap" rel="stylesheet">
<style>
  :root{
    --backdrop:#8aa9d3;
    --paper:#ffffff;
    --ink:#141414;
    --green:#3cb46e;
    --grid-line:#c9ddd1;
    --marble:#f1f1f1;
  }
  *{margin:0;padding:0;box-sizing:border-box}
  html,body{width:1200px;height:858px;overflow:hidden;background:var(--backdrop)}
  .board{position:relative;width:1200px;height:858px}
  .page{position:absolute;top:226px;width:265px;height:405px;background:var(--paper);overflow:hidden}
  .page--cover{left:40px;background:linear-gradient(160deg,#dff2e8 0%,#f4f6f5 50%,#eef5f3 100%)}
  .page--back{left:325px}
  .page--january{left:610px;background:linear-gradient(135deg,#f7f7f7,var(--marble))}
  .page--february{left:895px;background:linear-gradient(135deg,#f7f7f7,var(--marble))}

  .brand{position:absolute;left:20px;top:20px;display:flex;align-items:flex-start;gap:6px;font-family:"Saira Condensed",sans-serif;font-weight:500;color:var(--ink)}
  .brand__mark{width:10px;height:10px;background:var(--green);margin-top:10px}
  .brand__name{display:block;font-size:34px;line-height:30px;letter-spacing:1px}
  .brand__sub{display:block;font-size:13px;line-height:16px;letter-spacing:.5px}

  .year{position:absolute;font-family:"Archivo Black",sans-serif;line-height:1;letter-spacing:-4px}
  .year--top{left:20px;top:84px;font-size:90px;color:var(--ink)}
  .year--bottom{left:70px;top:146px;font-size:96px;color:var(--green)}
  .cover-label{position:absolute;left:22px;top:196px;font-family:"Saira Condensed",sans-serif;font-weight:700;font-size:17px;line-height:16px;color:var(--ink)}

  .photo{position:absolute;left:0;width:265px}
  .photo--cover{top:255px;height:150px;background:linear-gradient(160deg,#cfe6e4 0%,#6f8f95 40%,#2a2f33 75%,#b35a1f 100%)}
  .photo--sketch{top:110px;height:190px;background:linear-gradient(180deg,#ffffff 0%,#d4ecdc 55%,#a9d9b9 100%)}
  .photo--january{top:0;height:170px;background:linear-gradient(170deg,#b9a58d 0%,#8c7a66 35%,#d9c12f 70%,#3b3a3a 100%)}
  .photo--february{top:0;height:170px;background:linear-gradient(90deg,#c8c8c8 0%,#b5b5b5 40%,#2d4fa6 55%,#1f3f96 75%,#bdbdbd 100%)}

  .contact{position:absolute;left:20px;top:318px;font-family:"Montserrat",sans-serif;font-weight:500;font-size:11px;color:var(--ink);list-style:none}
  .contact li{display:flex;align-items:flex-start;gap:8px;margin-bottom:6px;line-height:13px}
  .contact svg{flex:none;margin-top:1px}

  .month{position:absolute;right:12px;top:180px;font-family:"Alfa Slab One",serif;font-weight:400;font-size:24px;line-height:30px;color:var(--ink)}
  .calendar{position:absolute;left:12px;top:220px;width:241px;display:grid;grid-template-columns:repeat(7,31px);column-gap:4px}
  .calendar__day{height:8px;background:var(--green);color:#fff;font-family:"Saira Condensed",sans-serif;font-weight:500;font-size:5px;line-height:8px;text-align:center;margin-bottom:3px;white-space:nowrap;overflow:hidden}
  .calendar__cell{height:28px;border:1px solid var(--grid-line);background:rgba(255,255,255,.75);margin-bottom:4px;padding:3px 4px;font-family:"Archivo Black",sans-serif;font-size:7px;line-height:9px;color:var(--ink)}
  .calendar__cell--empty{border-color:transparent;background:transparent}
</style>
</head>
<body>
<main class="board">

  <section class="page page--cover">
    <div class="brand"><span class="brand__mark"></span><div><span class="brand__name">TORVAN</span><span class="brand__sub">CONSTRUCTION LTD</span></div></div>
    <div class="year year--top">20</div>
    <div class="cover-label">CALE<br>NDAR</div>
    <div class="year year--bottom">25</div>
    <div class="photo photo--cover" role="img" aria-label="Double-exposure photo of an engineer in a hard hat blended with a city skyline"></div>
  </section>

  <section class="page page--back">
    <div class="brand"><span class="brand__mark"></span><div><span class="brand__name">TORVAN</span><span class="brand__sub">CONSTRUCTION LTD</span></div></div>
    <div class="photo photo--sketch" role="img" aria-label="Green sketch of a building under construction with tower cranes"></div>
    <ul class="contact">
      <li><svg width="10" height="10" viewBox="0 0 24 24"><path fill="#141414" d="M6.6 10.8a15 15 0 0 0 6.6 6.6l2.2-2.2c.3-.3.7-.4 1-.2 1.1.4 2.3.6 3.6.6.6 0 1 .4 1 1V20c0 .6-.4 1-1 1A17 17 0 0 1 3 4c0-.6.4-1 1-1h3.5c.6 0 1 .4 1 1 0 1.3.2 2.5.6 3.6.1.3 0 .7-.2 1z"/></svg><span>+234 800 555 0142</span></li>
      <li><svg width="10" height="12" viewBox="0 0 24 24"><path fill="#141414" d="M12 2a7 7 0 0 0-7 7c0 5.3 7 13 7 13s7-7.7 7-13a7 7 0 0 0-7-7zm0 9.5A2.5 2.5 0 1 1 12 6.5a2.5 2.5 0 0 1 0 5z"/></svg><span>14B Marlow Street,<br>Garki, Abuja Nigeria</span></li>
      <li><svg width="10" height="10" viewBox="0 0 24 24"><path fill="#141414" d="M2 5h20v14H2zm2 2v.5l8 5 8-5V7z"/></svg><span>info@torvanbuild.com</span></li>
    </ul>
  </section>

  <section class="page page--january">
    <div class="photo photo--january" role="img" aria-label="Team of site workers in hard hats and safety vests under a flyover"></div>
    <h2 class="month">January</h2>
    <div class="calendar">
      <div class="calendar__day">SUNDAY</div><div class="calendar__day">MONDAY</div><div class="calendar__day">TUESDAY</div><div class="calendar__day">WEDNESDAY</div><div class="calendar__day">THURSDAY</div><div class="calendar__day">FRIDAY</div><div class="calendar__day">SATURDAY</div>
      <div class="calendar__cell"></div><div class="calendar__cell"></div><div class="calendar__cell"></div><div class="calendar__cell">1</div><div class="calendar__cell">2</div><div class="calendar__cell">3</div><div class="calendar__cell">4</div>
      <div class="calendar__cell">5</div><div class="calendar__cell">6</div><div class="calendar__cell">7</div><div class="calendar__cell">8</div><div class="calendar__cell">9</div><div class="calendar__cell">10</div><div class="calendar__cell">11</div>
      <div class="calendar__cell">12</div><div class="calendar__cell">13</div><div class="calendar__cell">14</div><div class="calendar__cell">15</div><div class="calendar__cell">16</div><div class="calendar__cell">17</div><div class="calendar__cell">18</div>
      <div class="calendar__cell">19</div><div class="calendar__cell">20</div><div class="calendar__cell">21</div><div class="calendar__cell">22</div><div class="calendar__cell">23</div><div class="calendar__cell">24</div><div class="calendar__cell">25</div>
      <div class="calendar__cell">26</div><div class="calendar__cell">27</div><div class="calendar__cell">28</div><div class="calendar__cell">29</div><div class="calendar__cell">30</div><div class="calendar__cell">31</div><div class="calendar__cell calendar__cell--empty"></div>
    </div>
  </section>

  <section class="page page--february">
    <div class="photo photo--february" role="img" aria-label="Aerial view of a yellow truck and crew laying fresh asphalt on a road"></div>
    <h2 class="month">Feburary</h2>
    <div class="calendar">
      <div class="calendar__day">SUNDAY</div><div class="calendar__day">MONDAY</div><div class="calendar__day">TUESDAY</div><div class="calendar__day">WEDNESDAY</div><div class="calendar__day">THURSDAY</div><div class="calendar__day">FRIDAY</div><div class="calendar__day">SATURDAY</div>
      <div class="calendar__cell"></div><div class="calendar__cell"></div><div class="calendar__cell"></div><div class="calendar__cell"></div><div class="calendar__cell"></div><div class="calendar__cell"></div><div class="calendar__cell">1</div>
      <div class="calendar__cell">2</div><div class="calendar__cell">3</div><div class="calendar__cell">4</div><div class="calendar__cell">5</div><div class="calendar__cell">6</div><div class="calendar__cell">7</div><div class="calendar__cell">8</div>
      <div class="calendar__cell">9</div><div class="calendar__cell">10</div><div class="calendar__cell">11</div><div class="calendar__cell">12</div><div class="calendar__cell">13</div><div class="calendar__cell">14</div><div class="calendar__cell">15</div>
      <div class="calendar__cell">16</div><div class="calendar__cell">17</div><div class="calendar__cell">18</div><div class="calendar__cell">19</div><div class="calendar__cell">20</div><div class="calendar__cell">21</div><div class="calendar__cell">22</div>
      <div class="calendar__cell">23</div><div class="calendar__cell">24</div><div class="calendar__cell">25</div><div class="calendar__cell">26</div><div class="calendar__cell">27</div><div class="calendar__cell">28</div><div class="calendar__cell calendar__cell--empty"></div>
    </div>
  </section>

</main>
</body>
</html>
```